Packaging and labelling for Swiss made Organic CBD Oil

Visit our website www.clearleafmerida.example
We have not put any product on yet as require packaging and label design .
Website will give you a great feel for the company and how we have used
the logo . The Vextora cbd product shown is a company similar to ourselves with similar core values , we liked the clean packaging design they have .

Im happy if you want use the mandala symbol in our logo separate from
KELVORA, to separate and use the mandala symbol as a larger icon than
it appears in our logo
Clean , Pure , organic feel. Like the product to look pharmaceutical and life changing not gimmicky.
Colours to go with or be the same as our logo colours
But not too cold and clinical
Bottle size 84mm x 25mm
Label size 75mm x 30mm
Box 30mm x 30mm x 100mm
6 products
Full Spectrum :
500mg CBD (5%)
1000mg CBD ( 10% )
1500mg CBD (15%)
2000mg CBD ( 20% )
Broad spectrum THC Free
500mg CBD (5%)
Pets
500mg Broad Spectrum THC Free
Updates

Would like the design to be more modern than traditional

LABEL Information Front of Bottle - Logo KELVORA & Mandala - Mandala can be used separately as design symbol Organic Cannabis Oil 1500mg CBD (15%) Ful Spectrum 10ml Back of bottle Ingredients: Organic Cannabis Oil Extract Organic Sunflower Seed Oil THC - 0.2% Certified Swiss Organic Cultivation Shake well before use. Store in a cool , dry place and out of the each of children BOX information Front and rear Logo - KELVORA & Mandala - Mandala can be used separately as a design symbol Organic Cannabis Oil 1500mg CBD (15%) Full Spectrum Sides x 2 This product is a food supplement and is not intended to diagnose, treat, cure or prevent any disease If you are pregnant, lactating or taking any medication consult your health care practitioner Suitable for vegetarians and vegans Ingredients Organic Cannabis Oil extract Organis Sunflower Oil Store in a cool ,dry place, out of the reach of children Recommended Use 1-5 drops ( 1 drop = 7.5mg CBD ) Subject to body weight and personal requirement - visit www.clearleafmerida for more information 100% Natural 100% Organic GMO free 100% Vegan ( symbol with each ) Expiry date see bottle label Cultivated and manufactured in Switzerland

Target Market(s)

age 40 - 80

Font styles to use
Other font styles liked:
• In our website we have used Open Sans for the copy and Lato for headings .

Requirements
Must have
• look like an Industry leader
Kelvora will change the quality of peoples lives and in some cases may
even save lives so want look powerful and credible
Our Mission is - Through Delivering Pure , Premium , Organic products we will educate, inform and help people achieve healthier , happier lifestyles
Nice to have
• Colours to look good with our logo colours or be the same as our logo
colours
Logo Font - Avenir Black and Avenir Book

Font used in website - Content - Open Sans / Headings - Lato
If you have another font for the packaging information that will go well with
our logo, I'm happy for you to use your skills

```html
<!DOCTYPE html>
<html lang="en">
<head>
<meta charset="utf-8">
<title>Kelvora Organic Cannabis Oil – Packaging</title>
<link rel="stylesheet" href="https://fonts.googleapis.com/css2?family=Open+Sans:wght@300;400;600;700&display=swap">
<style>
  :root {
    --stage: #d8d8d8;
    --panel-black: #0b0b0b;
    --panel-glow: #2a2a2a;
    --logo-grey: #a9a9a9;
    --text-light: #e6e6e6;
    --text-soft: #cfcfcf;
    --organic-green: #6cb35a;
    --swiss-red: #d8262e;
    --white: #ffffff;
  }
  * { box-sizing: border-box; margin: 0; padding: 0; }
  html, body {
    width: 1200px; height: 1001px; overflow: hidden;
    background: var(--stage);
    font-family: "Open Sans", Arial, sans-serif;
  }
  .canvas { position: relative; width: 1200px; height: 1001px; }

  .panel {
    position: absolute;
    background: radial-gradient(ellipse at 70% 20%, var(--panel-glow) 0%, var(--panel-black) 60%);
    color: var(--text-light);
    overflow: hidden;
  }
  .box-front { left: 290px; top: 150px; width: 220px; height: 700px; border-right: 1px solid #222; }
  .box-side  { left: 510px; top: 150px; width: 220px; height: 700px; }
  .bottle-label { left: 770px; top: 420px; width: 380px; height: 152px; }

  .mandala-field { position: absolute; inset: 0; }

  .brand {
    position: absolute;
    font-weight: 700; color: var(--logo-grey);
    letter-spacing: 1px;
  }
  .box-front .brand { left: 24px; top: 80px; font-size: 30px; }

  .organic-row { position: absolute; display: flex; align-items: center; gap: 6px; }
  .organic-tag {
    background: var(--organic-green); color: var(--white);
    font-weight: 700; line-height: 1; padding: 3px 6px;
  }
  .swiss-mark {
    background: var(--swiss-red); position: relative;
  }
  .swiss-mark::before, .swiss-mark::after {
    content: ""; position: absolute; background: var(--white);
    left: 50%; top: 50%; transform: translate(-50%, -50%);
  }
  .swiss-mark::before { width: 60%; height: 20%; }
  .swiss-mark::after  { width: 20%; height: 60%; }

  .box-front .organic-row { left: 24px; top: 340px; }
  .box-front .organic-tag { font-size: 22px; }
  .box-front .swiss-mark { width: 24px; height: 24px; }

  .product-name { position: absolute; font-weight: 300; color: var(--text-light); }
  .box-front .product-name { left: 22px; top: 376px; font-size: 32px; }

  .strength { position: absolute; font-weight: 300; color: var(--text-light); line-height: 1.25; }
  .box-front .strength { left: 24px; top: 540px; font-size: 22px; }

  .origin { position: absolute; left: 24px; bottom: 60px; font-size: 16px; font-weight: 300; color: var(--text-soft); }

  .side-copy {
    position: absolute; left: 20px; top: 250px; right: 18px;
    font-size: 11.5px; font-weight: 300; line-height: 1.35; color: var(--text-light);
  }
  .side-copy p { margin-bottom: 10px; }
  .side-copy strong { font-weight: 600; }
  .volume { position: absolute; left: 80px; bottom: 30px; font-size: 14px; font-weight: 300; color: var(--text-soft); }

  .bottle-label .brand { left: 22px; top: 18px; font-size: 26px; }
  .bottle-label .organic-row { left: 22px; top: 70px; }
  .bottle-label .organic-tag { font-size: 17px; }
  .bottle-label .swiss-mark { width: 19px; height: 19px; }
  .bottle-label .product-name { left: 22px; top: 94px; font-size: 24px; }
  .bottle-label .strength { left: 220px; top: 88px; font-size: 15px; }
</style>
</head>
<body>
<main class="canvas">

  <section class="panel box-front" aria-label="Box front panel">
    <div class="mandala-field" role="img" aria-label="Large faint mandala brand symbol as background decoration"></div>
    <div class="brand">KELVORA</div>
    <div class="organic-row">
      <span class="organic-tag">ORGANIC</span>
      <span class="swiss-mark" role="img" aria-label="Swiss made mark"></span>
    </div>
    <div class="product-name">Cannabis Oil</div>
    <div class="strength">500 mg CBD (5%)<br>Broad Spectrum</div>
    <div class="origin">Made in Switzerland</div>
  </section>

  <section class="panel box-side" aria-label="Box side panel">
    <div class="mandala-field" role="img" aria-label="Large faint mandala brand symbol as background decoration"></div>
    <div class="side-copy">
      <p>This product is a food supplement and is not intended to diagnose, treat, cure or prevent any disease.</p>
      <p>If you are pregnant, lactating or taking any medication consult your health care practitioner.</p>
      <p>Suitable for vegetarians and vegans.</p>
      <p><strong>Ingredients:</strong> Organic Cannabis Oil Extract, Organic Sunflower Oil</p>
      <p>Store in a cool, dry place, out of the reach of children.</p>
      <p><strong>Batch No and Lab Results</strong><br>Visit <strong>www.kelvoraorganic.example</strong> for independent third party lab test results for this product</p>
      <p>Batch No and expiry date see label on bottom of box</p>
    </div>
    <div class="volume">10 ml</div>
  </section>

  <section class="panel bottle-label" aria-label="Bottle label">
    <div class="mandala-field" role="img" aria-label="Faint mandala brand symbol as background decoration"></div>
    <div class="brand">KELVORA</div>
    <div class="organic-row">
      <span class="organic-tag">ORGANIC</span>
      <span class="swiss-mark" role="img" aria-label="Swiss made mark"></span>
    </div>
    <div class="product-name">Cannabis Oil</div>
    <div class="strength">500 mg CBD (5%)<br>Broad Spectrum</div>
  </section>

</main>
</body>
</html>
```